Brightwick Music Studio needs a promotional postcard design

We are looking for a postcard design for a small business that provides clients with private music lesson instruction. We are looking for a design that will convey the message of "music is fun for kids" that will appeal to parents and encourage them to sign up. We have a company logo that should be used and our color scheme is teal and turquoise. All of our contact info should be displayed as well.

Target Market(s)

Parents with young kids

Contact Information for Business Card

web: www.brightwickmusicstudio.example
email: lessons@brightwickmusicstudio.example
phone: 202-555-0147

Font styles to use
Serif
Sans Serif

Colors
33b8a4
86cfc6
0456a4
87cfc6

Requirements
Must have
• Music lessons in your home
• Creating little stars one at a time
• Sign Up Now
• Please use these images:
Nice to have
• Something like this sample postcard:

```html
<!DOCTYPE html>
<html lang="en">
<head>
<meta charset="utf-8">
<title>Brightwick Music Studio – Postcard</title>
<link rel="stylesheet" href="https://fonts.googleapis.com/css2?family=Alegreya:wght@500&family=Bebas+Neue&family=Fondamento&family=Montserrat:wght@500&display=swap">
<style>
  :root {
    --teal: #4fb8bd;
    --teal-deep: #3aa7ac;
    --white: #ffffff;
    --ink: #0b0b0b;
    --backdrop: #ecebe8;
    --rule: #c9c9c9;
  }
  * { box-sizing: border-box; margin: 0; padding: 0; }
  html, body { width: 1200px; height: 698px; overflow: hidden; }
  body { background: var(--backdrop); position: relative; font-family: "Montserrat", sans-serif; }

  .postcard {
    position: absolute; top: 149px; width: 478px; height: 400px; overflow: hidden;
    box-shadow: 0 3px 10px rgba(0,0,0,.25);
  }
  .postcard--front { left: 106px; background: var(--ink); }
  .postcard--back { left: 616px; background: var(--teal); }

  /* front */
  .stage-photo {
    position: absolute; inset: 0 0 81px 0;
    background: radial-gradient(ellipse at 68% 45%, #6b4a3a 0%, #2a1d18 28%, #0d0b0b 55%, #050505 100%);
  }
  .brand { position: absolute; text-align: center; color: var(--teal); }
  .brand__mark { display: block; margin: 0 auto; border-radius: 50%; background: var(--teal); }
  .brand__name { font-family: "Alegreya", serif; font-weight: 500; line-height: 1; white-space: nowrap; }
  .brand__tagline { font-family: "Montserrat", sans-serif; font-weight: 500; letter-spacing: .3em; white-space: nowrap; }

  .postcard--front .brand { left: 40px; top: 44px; width: 172px; }
  .postcard--front .brand__mark { width: 76px; height: 76px; margin-bottom: 32px; }
  .postcard--front .brand__name { font-size: 34px; }
  .postcard--front .brand__tagline { font-size: 11.5px; margin-top: 10px; }

  .slogan-band {
    position: absolute; left: 0; right: 0; bottom: 0; height: 81px; background: var(--teal);
  }
  .slogan {
    position: absolute; left: 97px; right: 18px; top: 18px; text-align: center;
    font-family: "Fondamento", cursive; font-size: 34px; color: var(--white);
    line-height: 1.2; white-space: nowrap;
  }
  .kid-photo--front {
    position: absolute; left: 0; top: 257px; width: 85px; height: 143px;
    background: linear-gradient(180deg, #b79a80 0%, #8a6c58 40%, #3a3436 75%, #2a2628 100%);
    border-radius: 40px 40px 0 0;
  }

  /* back */
  .address-side { position: absolute; inset: 0; }
  .postcard--back .brand { left: 16px; top: 26px; width: 160px; color: var(--white); }
  .postcard--back .brand__mark { width: 70px; height: 70px; background: var(--white); margin-bottom: 28px; }
  .postcard--back .brand__name { font-size: 31px; }
  .postcard--back .brand__tagline { font-size: 11px; margin-top: 9px; }

  .kid-photo--back {
    position: absolute; left: 50px; top: 200px; width: 110px; height: 120px;
    background: linear-gradient(180deg, #3a2a24 0%, #d63a2e 30%, #c7332a 70%, #2d2a2a 100%);
    border-radius: 30px 30px 6px 6px;
  }
  .contact { position: absolute; left: 10px; top: 322px; width: 172px; text-align: center; color: var(--white); font-family: "Bebas Neue", sans-serif; }
  .contact__phone {
    display: block; font-size: 25px; line-height: 1; padding: 4px 0 2px;
    border-top: 1.5px solid var(--white); border-bottom: 1.5px solid var(--white);
    margin: 0 12px;
  }
  .contact__line { display: block; font-size: 11.5px; line-height: 1.35; letter-spacing: .01em; white-space: nowrap; }
  .contact__line:first-of-type { margin-top: 5px; }

  .address__to { position: absolute; left: 276px; top: 104px; font-size: 9px; color: var(--ink); }
  .stamp-box { position: absolute; left: 389px; top: 36px; width: 50px; height: 50px; border: 1px solid var(--rule); }
  .address__line { position: absolute; left: 285px; width: 152px; height: 1px; background: var(--rule); }
</style>
</head>
<body>

<section class="postcard postcard--front" aria-label="Postcard front">
  <div class="stage-photo" role="img" aria-label="Photo of a young girl playing the violin on stage against a dark curtain"></div>
  <div class="brand">
    <span class="brand__mark"></span>
    <div class="brand__name">Brightwick</div>
    <div class="brand__tagline">MUSIC STUDIO</div>
  </div>
  <div class="slogan-band">
    <p class="slogan">music is fun for kids</p>
  </div>
  <div class="kid-photo--front" role="img" aria-label="Photo of a smiling girl making a peace sign"></div>
</section>

<section class="postcard postcard--back" aria-label="Postcard back">
  <svg class="address-side" viewBox="0 0 478 400" width="478" height="400" aria-hidden="true">
    <path d="M270 0 C215 30 183 85 193 140 L200 205 C160 245 155 335 290 400 L478 400 L478 0 Z" fill="#ffffff"/>
    <circle cx="228" cy="170" r="36" fill="#4fb8bd"/>
  </svg>

  <div class="brand">
    <span class="brand__mark"></span>
    <div class="brand__name">Brightwick</div>
    <div class="brand__tagline">MUSIC STUDIO</div>
  </div>

  <div class="kid-photo--back" role="img" aria-label="Photo of a girl in a red dress dancing with a violin"></div>

  <div class="contact">
    <span class="contact__phone">202-555-0147</span>
    <span class="contact__line">LESSONS@BRIGHTWICKMUSICSTUDIO.EXAMPLE</span>
    <span class="contact__line">WWW.BRIGHTWICKMUSICSTUDIO.EXAMPLE</span>
  </div>

  <div class="stamp-box"></div>
  <span class="address__to">To</span>
  <span class="address__line" style="top:144px"></span>
  <span class="address__line" style="top:168px"></span>
  <span class="address__line" style="top:190px"></span>
  <span class="address__line" style="top:215px"></span>
</section>

</body>
</html>
```